Business Card Design for Marketing Firm

Looking for business card design for higher end marketing firm. Clean but impressionable/trendy. We are a marketing firm that represents manufacturers in the foodservice equipment and supply industry. Our customers are end users such has hotels, restaurants, country clubs, convention centers and casinos as well as distributors of restaurants supplies and equipment, and manufacturers of foodservice equipment and supplies.
Target Market(s)
Hotels, Restaurants, Supply & Equipment Distributors, Foodservice Manufacturers
Industry/Entity Type
Foodservice/Hospitality
Contact Information for Business Card
Name, Title, Contact Number, Email, Website, Social Media, Address
Requirements
Must have
- Clean & Simple but Serious and Impressionable

```html
<!DOCTYPE html>
<html lang="en">
<head>
<meta charset="utf-8">
<title>Meridian Hospitality Reps – Business Card</title>
<link href="https://fonts.googleapis.com/css2?family=Libre+Baskerville:wght@400;700&family=Arimo:wght@400&display=swap" rel="stylesheet">
<style>
  :root {
    --navy: #0b0a7c;
    --navy-deep: #06066a;
    --paper: #f6f6f8;
    --ink: #1c1c24;
    --stage: #2a2b2e;
    --white: #ffffff;
    --serif: "Libre Baskerville", Georgia, serif;
    --sans: "Arimo", Arial, sans-serif;
  }
  * { box-sizing: border-box; margin: 0; padding: 0; }
  html, body { width: 1200px; height: 912px; overflow: hidden; }
  body { background: var(--stage); position: relative; font-family: var(--sans); }

  .card {
    position: absolute; top: 306px; width: 530px; height: 300px;
    border-radius: 22px; overflow: hidden;
  }

  /* Back side */
  .card-back { left: 40px; background: var(--navy); color: var(--white); }
  .back-brand {
    position: absolute; left: 0; right: 0; top: 104px; text-align: center;
    font-family: var(--serif); font-weight: 700; font-size: 40px; letter-spacing: 1px;
  }
  .back-web {
    position: absolute; left: 0; right: 0; top: 212px; text-align: center;
    font-size: 13px; letter-spacing: 3px;
  }

  /* Front side */
  .card-front { left: 630px; background: var(--paper); color: var(--ink); }
  .brand {
    position: absolute; right: 34px; top: 40px; text-align: right;
    font-family: var(--serif); color: var(--navy);
  }
  .brand-name { font-size: 19px; font-weight: 700; letter-spacing: 0.5px; padding-bottom: 4px; border-bottom: 1.5px solid var(--navy); }
  .brand-sub { font-size: 10px; letter-spacing: 1px; margin-top: 3px; }

  .social { position: absolute; left: 30px; top: 40px; display: flex; gap: 6px; }
  .social span { width: 22px; height: 22px; border-radius: 50%; background: var(--navy); }

  .divider { position: absolute; left: 150px; right: 60px; top: 140px; height: 1px; background: var(--ink); }

  .address {
    position: absolute; right: 40px; top: 156px; text-align: right;
    font-size: 13px; line-height: 1.35;
  }

  .person { position: absolute; left: 44px; top: 150px; }
  .person-name { font-family: var(--serif); font-weight: 700; font-size: 26px; color: var(--navy); letter-spacing: 0.5px; }
  .person-title { font-size: 14px; color: #555; margin-top: 2px; padding-bottom: 6px; border-bottom: 1px solid var(--ink); width: 240px; }
  .contacts { list-style: none; margin-top: 8px; font-size: 15px; }
  .contacts li { display: flex; align-items: center; gap: 8px; line-height: 1.3; }
  .contacts svg { width: 13px; height: 13px; fill: var(--navy); flex: none; }

  .band { position: absolute; left: 0; right: 0; bottom: 0; height: 22px; background: var(--navy); }
  .band::before { content: ""; position: absolute; left: 0; right: 0; top: -7px; height: 2px; background: var(--navy); }
</style>
</head>
<body>
  <section class="card card-back">
    <div class="back-brand">Meridian</div>
    <div class="back-web">www.meridianreps.com</div>
  </section>

  <section class="card card-front">
    <div class="social" aria-label="Social media">
      <span></span><span></span><span></span>
    </div>
    <div class="brand">
      <div class="brand-name">MERIDIAN HOSPITALITY</div>
      <div class="brand-sub">REPS</div>
    </div>
    <div class="divider"></div>
    <address class="address" style="font-style:normal">
      4120 Harbor View Lane<br>Glenwood, NY 10000
    </address>
    <div class="person">
      <div class="person-name">DANIEL CARTER</div>
      <div class="person-title">President</div>
      <ul class="contacts">
        <li><svg viewBox="0 0 16 16"><path d="M3 1l3 3-2 2c1 2 3 4 5 5l2-2 3 3-2 3C7 15 1 9 1 3z"/></svg>(555) 0142-7780</li>
        <li><svg viewBox="0 0 16 16"><path d="M1 3h14v10H1zM1 3l7 6 7-6"/></svg>name@meridianreps.com</li>
        <li><svg viewBox="0 0 16 16"><circle cx="8" cy="8" r="7"/></svg>www.meridianreps.com</li>
      </ul>
    </div>
    <div class="band"></div>
  </section>
</body>
</html>
```